Web and Logo Design for eCommerce site

We're launching a sister brand and require a full design for the site.

The site must have an established feel and appeal to corporate and institutional buyers.
Updates

Just a note about the wireframe design:

The Search & Rescue / Coast Guard / NVDK, etc. in the header area aren't buttons or menu items, but rather just info (along the lines of a tagline).  Sort of a "who we serve" sort of thing.

Worth noting is that it's specifically geared towards LARGE BUYERS.  For example, a police force buying 200 headlamps and 85 pairs of gloves.  So they'll register + sign in and then add a bunch of items to a RFQ.

Aim for a professional, masculine design.

Target Market(s)

We will be selling outdoor gear to the military, law enforcement, fire and rescue and first responders.

Requirements
Must have
• We require:
- Logo (vector based)

Site:
- template page
* main site template, re-skinned version of our current site
* horizontal drop-down menu
- product listings page
* thumbnail view of products
- product details page
* including elements such as product image, color/size selector, descriptions and specs (again, based loosely on our current website)
- account management page
* illustrating basic data entry styles for text box, buttons, grid, etc.

The site needs to be given a responsive design, so 2 versions of each design should be presented for desktop + mobile views.

Additional funds are available if the designer is able to fully implement the designs into a responsive framework such as bootstrap.

Nice to have
• Clean, professional design similar to:

http://military.trailvexagear.com/gov/accessories/gloves.html

http://leaf.ombrivo.com/ProductFind.aspx?language=EN&category=Hardshell&subcat=Waterproof_Jackets

```html
<!DOCTYPE html>
<html lang="en">
<head>
<meta charset="utf-8">
<title>Norvex – Canadian Outdoor Pro Supply</title>
<link href="https://fonts.googleapis.com/css2?family=Open+Sans:wght@400;600;700&family=Oswald:wght@500;700&display=swap" rel="stylesheet">
<style>
:root{
  --red:#d62a26;
  --ink:#222;
  --dark:#2a2a2a;
  --nav:#333;
  --side:#e2e2e2;
  --line:#cfcfcf;
  --muted:#777;
  --yellow:#f2b01e;
  --green:#4caf3d;
  --white:#fff;
}
*{box-sizing:border-box;margin:0;padding:0}
html,body{width:863px;height:1200px;overflow:hidden}
body{font-family:"Open Sans",Arial,sans-serif;color:var(--ink);background:var(--white);font-size:8px;position:relative}
ul{list-style:none}

.topbar{height:20px;background:var(--dark);display:flex;align-items:center;justify-content:space-between;padding:0 16px;color:#ccc;font-size:7.5px}
.topbar .serve b{color:var(--red);font-weight:700}
.topbar .quote{background:var(--green);color:var(--white);height:20px;display:flex;align-items:center;padding:0 14px;font-weight:700;font-size:7px}

.masthead{height:46px;display:flex;align-items:center;justify-content:space-between;padding:0 16px}
.brand{display:flex;align-items:center;gap:8px}
.brand-mark{width:22px;height:22px;background:var(--red)}
.brand-name{font-family:"Oswald",Arial,sans-serif;font-weight:700;font-size:28px;color:var(--ink);letter-spacing:1px}
.account{text-align:right;font-size:8px;font-weight:600;line-height:1.5}
.account .call{color:var(--red)}

.mainnav{height:27px;display:flex;margin:0 16px;background:var(--nav)}
.who{width:205px;background:var(--red);color:var(--white);font-family:"Oswald",Arial,sans-serif;font-size:11px;display:flex;align-items:center;justify-content:space-between;padding:0 12px}
.menu{display:flex;align-items:stretch;padding-left:14px}
.menu li{color:#ddd;font-size:8px;font-weight:600;display:flex;align-items:center;padding:0 9px}
.menu li.active{background:var(--red);color:var(--white)}

.page{display:flex;gap:17px;margin:0 16px;height:857px}
.sidebar{width:205px;background:var(--side);padding:12px}
.sidebar h3{font-size:7.5px;font-weight:700;margin:10px 0 4px}
.sidebar h3:first-child{margin-top:0}
.sidebar li{font-size:6.8px;color:var(--muted);line-height:12px}

.content{flex:1;padding-top:10px}
.hero{height:250px;border:1px solid var(--line);display:flex;position:relative}
.hero-copy{width:48%;padding:36px 20px}
.hero-copy h1{font-family:"Oswald",Arial,sans-serif;font-weight:500;font-size:22px;line-height:1.15}
.hero-copy h1 span{color:var(--red);display:block}
.hero-copy p{font-size:7.5px;color:var(--muted);line-height:1.5;margin:10px 0 14px}
.btn-more{display:inline-block;background:var(--yellow);font-weight:700;font-size:7.5px;padding:6px 12px}
.hero-img{flex:1;margin:12px;background:
  radial-gradient(circle at 30% 60%,#2e2a20 0,#2e2a20 18%,transparent 19%),
  radial-gradient(circle at 70% 35%,#7d7a55 0,#7d7a55 16%,transparent 17%),
  radial-gradient(circle at 80% 78%,#a08f6a 0,#a08f6a 12%,transparent 13%),
  linear-gradient(135deg,#e9e6de,#cfcabd)}
.dots{position:absolute;bottom:-13px;left:50%;transform:translateX(-50%);display:flex;gap:5px}
.dots i{width:6px;height:6px;border-radius:50%;background:#bbb}
.dots i.on{background:var(--red)}

.sortbar{margin-top:20px;height:20px;border:1px solid var(--line);display:flex;align-items:center;justify-content:space-between;padding:0 8px;font-size:6.5px;font-weight:700}
.sortbar .sel{display:inline-block;width:56px;height:11px;border:1px solid var(--line);vertical-align:middle;margin-left:4px}
.pager{display:flex;gap:6px;align-items:center}
.pager b{background:var(--red);color:var(--white);padding:1px 4px}

.grid{display:grid;grid-template-columns:repeat(4,1fr);gap:10px 12px;margin-top:12px}
.tile{border:1px solid var(--line);padding:8px;height:160px}
.thumb{height:96px;background:#eee}
.thumb.rescue{background:radial-gradient(circle at 50% 55%,#2f6fae 0,#2f6fae 30%,#e0b43a 31%,#e0b43a 40%,#f3f3f3 41%)}
.thumb.boot{background:radial-gradient(ellipse at 50% 55%,#b59a72 0,#b59a72 32%,#f3f3f3 33%)}
.thumb.camo{background:radial-gradient(ellipse at 50% 50%,#7d7655 0,#6a6a48 34%,#f3f3f3 35%)}
.thumb.tent{background:linear-gradient(170deg,#f3f3f3 35%,#4f6a3a 36%,#4f6a3a 58%,#f3f3f3 59%)}
.thumb.camp{background:radial-gradient(ellipse at 50% 55%,#8a8a8a 0,#5a5a5a 32%,#f3f3f3 33%)}
.thumb.glove{background:radial-gradient(ellipse at 50% 55%,#3a3a30 0,#5b5a45 32%,#f3f3f3 33%)}
.thumb.brand{background:radial-gradient(ellipse at 50% 55%,#6f6a4f 0,#4c4a36 32%,#f3f3f3 33%)}
.thumb.ramp{background:linear-gradient(160deg,#f3f3f3 30%,#2c2c2c 31%,#2c2c2c 60%,#f3f3f3 61%)}
.tile h4{color:var(--red);font-size:8px;font-weight:700;margin:7px 0 3px}
.tile p{font-size:6.5px;color:var(--muted);line-height:1.4}
.bottombar{margin-top:20px;height:20px;border:1px solid var(--line)}

.footer{position:absolute;top:978px;left:0;width:863px;height:184px;background:var(--dark);color:#bbb;padding:20px 26px;display:flex;justify-content:space-between}
.cols{display:grid;grid-template-columns:repeat(3,150px);row-gap:16px;align-content:start}
.cols h5,.signup h5{color:var(--white);font-size:8px;font-weight:700;margin-bottom:5px;padding-bottom:4px;border-bottom:2px solid var(--red);width:110px}
.cols li{font-size:7px;line-height:12px}
.signup{width:270px}
.signup h5{width:100%;border-bottom:1px solid #444}
.signup .block{margin-bottom:10px}
.field{display:flex;gap:6px}
.field .input{flex:1;height:16px;background:var(--white)}
.field .go{background:var(--red);color:var(--white);font-size:7px;font-weight:700;padding:0 12px;display:flex;align-items:center}
.social{display:flex;gap:6px}
.social i{width:16px;height:16px;background:#555}
.legal{position:absolute;top:1162px;left:0;width:863px;height:38px;display:flex;align-items:center;justify-content:center;font-size:7px;color:var(--muted)}
</style>
</head>
<body>

<div class="topbar">
  <div class="serve"><b>Search &amp; Rescue</b> | Coast Guard | NVDK | Fire | Military | Law Enforcement</div>
  <div class="quote">REQUEST A QUOTE</div>
</div>

<header class="masthead">
  <div class="brand"><span class="brand-mark"></span><span class="brand-name">NORVEX</span></div>
  <div class="account">SIGN IN | CREATE ACCOUNT<br><span class="call">CALL: 123 456 7890</span></div>
</header>

<nav class="mainnav">
  <div class="who">Who We Serve <span>&#9662;</span></div>
  <ul class="menu">
    <li class="active">Rescue Gear</li><li>Footwear</li><li>Clothing</li><li>Tents Mats Sleeping Bags</li><li>Camping Gear</li><li>Snow Sports</li><li>Brands</li>
  </ul>
</nav>

<div class="page">
  <aside class="sidebar">
    <h3>CATEGORY</h3>
    <ul><li>Rescue Gear</li><li>Footwear</li><li>Clothing</li><li>Tents Mats Sleeping Bags</li><li>Camping Gear</li><li>Snow Sports</li><li>Brands</li></ul>
    <h3>ORIGIN</h3>
    <ul><li>Lorem ipsum dolor</li><li>Sit amet consectetur</li><li>Adipiscing elit</li><li>Sed do eiusmod</li><li>Tempor incididunt</li><li>Ut labore et dolore</li><li>Magna aliqua</li></ul>
    <h3>PRODUCT HIGHLIGHTS</h3>
    <ul><li>Lorem ipsum dolor</li><li>Sit amet consectetur</li><li>Adipiscing elit</li><li>Sed do eiusmod</li><li>Tempor incididunt</li><li>Ut labore et dolore</li><li>Magna aliqua</li></ul>
    <h3>SIZE</h3>
    <ul><li>XS</li><li>S</li><li>M</li><li>L</li><li>XL</li><li>XXL</li><li>3XL</li></ul>
    <h3>SPORTS</h3>
    <ul><li>Lorem ipsum dolor</li><li>Sit amet consectetur</li><li>Adipiscing elit</li><li>Sed do eiusmod</li><li>Tempor incididunt</li></ul>
  </aside>

  <main class="content">
    <section class="hero">
      <div class="hero-copy">
        <h1>Canadian Outdoor<span>Pro Supply</span></h1>
        <p>Lorem ipsum dolor sit amet, consectetur adipiscing elit, sed do eiusmod tempor incididunt ut labore et dolore magna aliqua.</p>
        <span class="btn-more">LEARN MORE</span>
      </div>
      <div class="hero-img" role="img" aria-label="Assorted outdoor and tactical gear: boots, packs, helmet and clothing"></div>
      <div class="dots"><i class="on"></i><i></i><i></i><i></i></div>
    </section>

    <div class="sortbar">
      <span>SORT BY <span class="sel"></span></span>
      <span class="pager">PAGE <b>1</b> 2 3 4 5 &nbsp; &lsaquo; PREV | NEXT &rsaquo; &nbsp; SHOW ALL</span>
    </div>

    <div class="grid">
      <article class="tile"><div class="thumb rescue" role="img" aria-label="Rescue gear"></div><h4>Rescue Gear</h4><p>Lorem ipsum dolor sit amet consectetur adipiscing elit</p></article>
      <article class="tile"><div class="thumb boot" role="img" aria-label="Tan boot"></div><h4>Footwear</h4><p>Lorem ipsum dolor sit amet consectetur adipiscing elit</p></article>
      <article class="tile"><div class="thumb camo" role="img" aria-label="Camouflage jacket"></div><h4>Clothing</h4><p>Lorem ipsum dolor sit amet consectetur adipiscing elit</p></article>
      <article class="tile"><div class="thumb tent" role="img" aria-label="Green hammock tent"></div><h4>Tents Mats</h4><p>Lorem ipsum dolor sit amet consectetur adipiscing elit</p></article>
      <article class="tile"><div class="thumb camp" role="img" aria-label="Camping stove and cookware"></div><h4>Camping Gear</h4><p>Lorem ipsum dolor sit amet consectetur adipiscing elit</p></article>
      <article class="tile"><div class="thumb glove" role="img" aria-label="Tactical gloves"></div><h4>Gloves</h4><p>Lorem ipsum dolor sit amet consectetur adipiscing elit</p></article>
      <article class="tile"><div class="thumb brand" role="img" aria-label="Olive backpack"></div><h4>Brands</h4><p>Lorem ipsum dolor sit amet consectetur adipiscing elit</p></article>
      <article class="tile"><div class="thumb ramp" role="img" aria-label="Black folding ramp"></div><h4>Ramp</h4><p>Lorem ipsum dolor sit amet consectetur adipiscing elit</p></article>
    </div>
    <div class="bottombar"></div>
  </main>
</div>

<footer class="footer">
  <div class="cols">
    <div><h5>SHOP</h5><ul><li>Lorem ipsum</li><li>Lorem ipsum</li><li>Lorem ipsum</li></ul></div>
    <div><h5>CONTACT US</h5><ul><li>Lorem ipsum</li><li>Lorem ipsum</li><li>Lorem ipsum</li></ul></div>
    <div><h5>CUSTOMERS</h5><ul><li>Lorem ipsum</li><li>Lorem ipsum</li><li>Lorem ipsum</li></ul></div>
    <div><h5>BLOG</h5><ul><li>Lorem ipsum</li><li>Lorem ipsum</li><li>Lorem ipsum</li></ul></div>
    <div><h5>VIDEO</h5><ul><li>Lorem ipsum</li><li>Lorem ipsum</li><li>Lorem ipsum</li></ul></div>
    <div><h5>CULTURE</h5><ul><li>Lorem ipsum</li><li>Lorem ipsum</li><li>Lorem ipsum</li></ul></div>
  </div>
  <div class="signup">
    <div class="block"><h5>&#9993; EMAIL &amp; CATALOG SIGNUP</h5><div class="field"><span class="input"></span><span class="go">SIGN UP</span></div></div>
    <div class="block"><h5>&#9679; FIND A NORVEX</h5><div class="field"><span class="input"></span><span class="go">FIND</span></div></div>
    <div class="block"><h5>CONNECT</h5><div class="social"><i></i><i></i><i></i><i></i><i></i></div></div>
  </div>
</footer>

<div class="legal">Register | Terms of Use | Privacy Policy © 2014 norvex.com</div>

</body>
</html>
```